Real Estate Flyer

Hi - I am assisting a relative to sell a unit. I am looking to have a two page flyer designed (configured as a single page with back to back printing). I have uploaded two samples to give you an idea of the look and feel - one which relates to this property when originally purchased, the other for a different property.
The flyer should includes several key photos on the front along with the wording. The rear should include any secondary photos along with the floor plan.
The flyer should be close to A4 size.

Updates
Hi,
Industry/Entity Type
Real Estate
Look and feel
Each slider illustrates characteristics of the customer's brand and the style your logo design should communicate.

```html
<!DOCTYPE html>
<html lang="en">
<head>
<meta charset="utf-8">
<title>Oversized apartment in a lifestyle location</title>
<link rel="stylesheet" href="https://fonts.googleapis.com/css2?family=Ubuntu:wght@300;400;500;700&display=swap">
<style>
  :root {
    --bg-dark: #262626;
    --bg-mid: #353535;
    --text: #f2f2f2;
    --text-soft: #e4e4e4;
    --tick: #7fc242;
    --sky: #3c86d6;
    --wall: #c9a57a;
    --cream: #e9e3d4;
    --tile: #d8d8d6;
  }
  * { margin: 0; padding: 0; box-sizing: border-box; }
  html, body { width: 849px; height: 1200px; overflow: hidden; }
  body {
    font-family: "Ubuntu", sans-serif;
    color: var(--text);
    background: radial-gradient(ellipse at 50% 40%, var(--bg-mid), var(--bg-dark) 75%);
    position: relative;
  }
  .flyer { position: absolute; inset: 0; }
  .headline {
    position: absolute; left: 48px; top: 48px;
    font-size: 38px; font-weight: 500; letter-spacing: -0.5px;
  }
  .specs {
    position: absolute; right: 43px; top: 110px;
    font-size: 19px; font-weight: 400;
  }
  .photo { position: absolute; }
  .photo-hero {
    left: 50px; top: 152px; width: 756px; height: 346px;
    background: linear-gradient(100deg, var(--cream) 0%, #b9a385 30%, var(--wall) 50%, #a9683f 62%, #c5b295 72%, var(--sky) 85%, #6fa6e0 100%);
  }
  .photo-kitchen { left: 49px; top: 520px; width: 240px; height: 170px;
    background: linear-gradient(160deg, #f3f1ea, #dedad0 70%, #9a9384); }
  .photo-living { left: 307px; top: 520px; width: 240px; height: 170px;
    background: linear-gradient(180deg, #f2efe6 0%, #e4dfd2 60%, #8d8a86 100%); }
  .photo-bath { left: 565px; top: 520px; width: 240px; height: 170px;
    background: linear-gradient(180deg, #f4f4f2 0%, var(--tile) 70%, #9aa3ab 100%); }
  .inspect {
    position: absolute; top: 699px; left: 0; width: 849px;
    font-size: 29px; font-weight: 300;
  }
  .inspect span { position: absolute; white-space: nowrap; }
  .address {
    position: absolute; top: 768px; left: 0; width: 849px;
    text-align: center; font-size: 23px; font-weight: 500;
  }
  .summary {
    position: absolute; left: 49px; top: 814px; width: 760px;
    font-size: 15.3px; font-weight: 300; line-height: 19.3px; letter-spacing: -0.3px;
  }
  .features { position: absolute; list-style: none; font-size: 15px; font-weight: 300; letter-spacing: -0.3px; }
  .features li { position: absolute; padding-left: 18px; line-height: 19px; white-space: nowrap; }
  .features svg { position: absolute; left: 0; top: 3px; }
  .features-left { left: 64px; top: 0; }
  .features-right { left: 453px; top: 0; }
  .rates { position: absolute; left: 48px; top: 1050px; font-size: 14.5px; font-weight: 300; line-height: 19.4px; }
  .rates dt { float: left; clear: left; width: 139px; }
  .rates dd { float: left; }
  .contact { position: absolute; left: 440px; width: 384px; top: 1048px; text-align: center; font-weight: 300; }
  .contact-name { font-size: 32px; word-spacing: 34px; }
  .contact-note { font-size: 16px; margin-top: 2px; }
  .contact-phone { font-size: 32px; font-weight: 400; letter-spacing: 1.5px; margin-top: 4px; }
</style>
</head>
<body>
<main class="flyer">
  <h1 class="headline">Oversized apartment in a lifestyle location</h1>
  <p class="specs">2 BED | 2 BATH | 1 CAR</p>

  <div class="photo photo-hero" role="img" aria-label="Photo of the terrace with curved balcony and district views"></div>
  <div class="photo photo-kitchen" role="img" aria-label="Photo of the white kitchen"></div>
  <div class="photo photo-living" role="img" aria-label="Photo of the open living area"></div>
  <div class="photo photo-bath" role="img" aria-label="Photo of the tiled bathroom"></div>

  <p class="inspect">
    <span style="left:145px">Inspect :</span>
    <span style="left:283px">Sat 10:45 – 11:30</span>
    <span style="left:533px">Wed 12:00 – 12:30</span>
  </p>

  <h2 class="address">12/40-46 Laurel Street, HARBOUR JUNCTION</h2>

  <p class="summary">Peacefully positioned on the 5th floor of a refurbished security building, this superbly spacious residence combines modern, low maintenance apartment living with inviting prospects for the entertainer. Boasting a huge full-width terrace on-title, its sought-after setting in the heart of Harbour Junction offers the ultimate in lifestyle and convenience.</p>

  <ul class="features features-left">
    <li style="top:925px"><svg width="15" height="14" viewBox="0 0 15 14"><path d="M1 8 L5 12 L14 1" fill="none" stroke="var(--tick)" stroke-width="2.4"/></svg>Expansive open plan living and dining area</li>
    <li style="top:962px"><svg width="15" height="14" viewBox="0 0 15 14"><path d="M1 8 L5 12 L14 1" fill="none" stroke="var(--tick)" stroke-width="2.4"/></svg>Terrace features city and Pelican Bay glimpses</li>
    <li style="top:998px"><svg width="15" height="14" viewBox="0 0 15 14"><path d="M1 8 L5 12 L14 1" fill="none" stroke="var(--tick)" stroke-width="2.4"/></svg>Kitchen updated with Verano gas appliances</li>
  </ul>
  <ul class="features features-right">
    <li style="top:925px"><svg width="15" height="14" viewBox="0 0 15 14"><path d="M1 8 L5 12 L14 1" fill="none" stroke="var(--tick)" stroke-width="2.4"/></svg>Built-ins in both bedrooms, fully tiled bathrooms</li>
    <li style="top:962px"><svg width="15" height="14" viewBox="0 0 15 14"><path d="M1 8 L5 12 L14 1" fill="none" stroke="var(--tick)" stroke-width="2.4"/></svg>Internal laundry, secure parking, lift, outdoor<br>pool and gymnasium</li>
    <li style="top:1017px"><svg width="15" height="14" viewBox="0 0 15 14"><path d="M1 8 L5 12 L14 1" fill="none" stroke="var(--tick)" stroke-width="2.4"/></svg>Steps to station, Parkside Mall and Meridian Park</li>
  </ul>

  <dl class="rates">
    <dt>Water Rates:</dt><dd>$168.80/qtr</dd>
    <dt>Council Rates:</dt><dd>$205.75/qtr</dd>
    <dt>Strata Rates:</dt><dd>$1,457.92/qtr</dd>
    <dt>Estimated Rental:</dt><dd>$700.00 p/w</dd>
  </dl>

  <div class="contact">
    <p class="contact-name">Contact: Dana&nbsp;Whitfield</p>
    <p class="contact-note">(Assisting owner in Private Sale)</p>
    <p class="contact-phone">0400 555 318</p>
  </div>
</main>
</body>
</html>
```